co working space / serviced office/ business centre

Brevlo - brevlo.in, is a very young brand bieng run by 3 young entrepreneurs. We want to be become out of the league company delivering fabulous and beautiful serviced offices in India and abroad. We hire designers who have made spaces across the world. We want to get visiting card design which gives complete fresh look to the people who carries that card, has to be very impactful and should symbolise happy young and energetic brand. should be completely out of the box thinking of international level, should portray global brand image.

Target Market(s)

Startups, (Small, medium and large corporates)

Industry/Entity Type

Business

Contact Information for Business Card

Name, Email, Address, Mobile number, Landline number, website

Colors

Designer to choose colors to be used in the design.

Requirements
Must have
• Nice new shape
Nice to have
• We want creative cuts, different size and impactful brand clarity
Should not have
• Boring and regular design and shape

```html
<!DOCTYPE html>
<html lang="en">
<head>
<meta charset="utf-8">
<title>Brevlo Business Card</title>
<link href="https://fonts.googleapis.com/css2?family=Open+Sans:wght@400;600;800&display=swap" rel="stylesheet">
<style>
  :root {
    --stage: #3a3a3c;
    --ink: #111111;
    --black: #000000;
    --red: #e92d3a;
    --white: #ffffff;
    --grey: #6b6b6b;
  }
  * { margin: 0; padding: 0; box-sizing: border-box; }
  html, body { width: 1200px; height: 864px; overflow: hidden; }
  body {
    background: var(--stage);
    font-family: "Open Sans", sans-serif;
    position: relative;
  }
  .card {
    position: absolute;
    top: 277px;
    width: 540px;
    height: 310px;
    overflow: hidden;
    box-shadow: 0 10px 30px rgba(0,0,0,.45);
  }
  .card--back { left: 40px; background: var(--black); }
  .card--front { left: 620px; background: var(--white); }

  .brand {
    display: flex;
    align-items: center;
    gap: 12px;
    color: var(--red);
    font-weight: 800;
    letter-spacing: 4px;
    text-transform: uppercase;
  }
  .brand__dot {
    background: var(--red);
    border-radius: 50%;
    flex: none;
  }
  .card--back .brand {
    position: absolute;
    left: 0; right: 0; top: 105px;
    justify-content: center;
    font-size: 58px;
    line-height: 1;
  }
  .card--back .brand__dot { width: 34px; height: 34px; }
  .card--back .site {
    position: absolute;
    left: 0; right: 0; top: 232px;
    text-align: center;
    color: var(--white);
    font-size: 15px;
    font-weight: 600;
    letter-spacing: .5px;
  }

  .card__shapes { position: absolute; inset: 0; }
  .card--front .brand {
    position: absolute;
    left: 40px; top: 52px;
    font-size: 40px;
    line-height: 1;
  }
  .card--front .brand__dot { width: 24px; height: 24px; }
  .person { position: absolute; left: 52px; top: 128px; }
  .person__name { font-size: 20px; font-weight: 600; color: var(--ink); }
  .person__role { font-size: 13px; color: var(--grey); margin-top: 0; }
  .contacts {
    position: absolute;
    left: 52px; top: 200px;
    list-style: none;
    font-size: 14px;
    color: var(--grey);
    line-height: 22px;
  }
  .contacts li { display: flex; align-items: center; gap: 8px; }
  .contacts svg { width: 12px; height: 12px; fill: var(--red); flex: none; }
  .address {
    position: absolute;
    right: 26px; top: 222px;
    text-align: right;
    color: var(--white);
    font-size: 13.5px;
    line-height: 20px;
  }
</style>
</head>
<body>

<section class="card card--back" aria-label="Card back">
  <div class="brand"><span class="brand__dot"></span>Brevlo</div>
  <p class="site">www.brevlo.in</p>
</section>

<section class="card card--front" aria-label="Card front">
  <svg class="card__shapes" viewBox="0 0 540 310" preserveAspectRatio="none" aria-hidden="true">
    <polygon points="308,0 322,0 264,310 256,310" fill="var(--black)"/>
    <polygon points="330,0 540,0 540,310 276,310" fill="var(--red)"/>
  </svg>

  <div class="brand"><span class="brand__dot"></span>Brevlo</div>

  <div class="person">
    <p class="person__name">Rohan Kapoor</p>
    <p class="person__role">President</p>
  </div>

  <ul class="contacts">
    <li><svg viewBox="0 0 24 24"><path d="M6.6 10.8a15 15 0 0 0 6.6 6.6l2.2-2.2a1 1 0 0 1 1-.25 11.4 11.4 0 0 0 3.6.57 1 1 0 0 1 1 1V20a1 1 0 0 1-1 1A17 17 0 0 1 3 4a1 1 0 0 1 1-1h3.5a1 1 0 0 1 1 1c0 1.25.2 2.45.57 3.6a1 1 0 0 1-.25 1z"/></svg>01 012-345-6789</li>
    <li><svg viewBox="0 0 24 24"><path d="M7 1h10a2 2 0 0 1 2 2v18a2 2 0 0 1-2 2H7a2 2 0 0 1-2-2V3a2 2 0 0 1 2-2zm0 3v15h10V4z"/></svg>01 012-345-6780</li>
    <li><svg viewBox="0 0 24 24"><path d="M2 5h20v14H2zm2 2v.5l8 5 8-5V7z"/></svg>hello@brevlo.in</li>
    <li><svg viewBox="0 0 24 24"><path d="M12 2a10 10 0 1 0 0 20 10 10 0 0 0 0-20zm6.9 9h-3a15 15 0 0 0-1.3-5.6A8 8 0 0 1 18.9 11zM12 4c.9 1.2 1.8 3.7 1.9 7h-3.8c.1-3.3 1-5.8 1.9-7zM9.4 5.4A15 15 0 0 0 8.1 11h-3a8 8 0 0 1 4.3-5.6zM5.1 13h3a15 15 0 0 0 1.3 5.6A8 8 0 0 1 5.1 13zM12 20c-.9-1.2-1.8-3.7-1.9-7h3.8c-.1 3.3-1 5.8-1.9 7zm2.6-1.4a15 15 0 0 0 1.3-5.6h3a8 8 0 0 1-4.3 5.6z"/></svg>www.brevlo.in</li>
  </ul>

  <p class="address">Street Name, Suite 100<br>State, Zip Code, Country</p>
</section>

</body>
</html>
```